Leadership training for women Business + Spirit

I need a flyer for a leadership training to hand out after I've been doing public speaking. I would also like to send it as a PDF. so maybe A4 is a good size. I will probably also need a brochure, with some more in depth information, but to start with I like to just give them something so they get inspired to contact me for more information. You can see more of my style on www.brightmeadow.se . Its a training that combines business with spirit, heart with intellect. We focus both on strict leadership skills such as Setting objectives aligned with strategy, assess performance and spiritual practices such as meditation, connecting with your unique essence. I like the deign to communicate business and professional together with warmth, life and joy. Colourful with style. Empowerment. The attached style guide does not have to be followed strictly but please use it in combination with my site www.brightmeadow.se I've the logo in many different sizes. I've added the smallest one below. Use any images that you think might fit, doesn't have to be from my website, it could be from your resources. I've added some other images here in the brief too, I have many more but can't attach all of it :-).
Target Market(s)
Women in leadership positions age 30 - 60
Industry/Entity Type
Leadership
Look and feel

```html
<!DOCTYPE html>
<html lang="en">
<head>
<meta charset="utf-8">
<title>Bright Meadow – Leadership Flyer</title>
<link href="https://fonts.googleapis.com/css2?family=Libre+Caslon+Display&family=Lato:wght@400;700;900&display=swap" rel="stylesheet">
<style>
  :root {
    --navy: #15334f;
    --slate: #d4d9df;
    --grey-wave: #b9bcc0;
    --white: #ffffff;
    --ink: #15334f;
  }
  html, body { margin: 0; padding: 0; overflow: hidden; }
  body { width: 950px; height: 1200px; background: var(--white); font-family: "Lato", sans-serif; color: var(--ink); }
  .flyer { position: relative; width: 950px; height: 1200px; overflow: hidden; background: var(--white); }

  .header-wave { position: absolute; left: 0; top: 0; width: 950px; height: 250px; }
  .brand-mark { position: absolute; left: 140px; top: 35px; width: 150px; height: 150px; border: 2px solid var(--white); border-radius: 50%; box-sizing: border-box; }
  .brand-name { position: absolute; left: 310px; top: 62px; font-family: "Libre Caslon Display", serif; font-size: 82px; line-height: 1; color: var(--white); white-space: nowrap; letter-spacing: -1px; }

  .portrait { position: absolute; left: 38px; top: 269px; width: 211px; height: 250px; background: linear-gradient(160deg, #7a5a4a 0%, #a3816c 40%, #3b3f4a 100%); }
  .founder { position: absolute; left: 269px; top: 272px; width: 648px; }
  .founder-name { margin: 0 0 12px; font-size: 28px; font-weight: 900; }
  .founder p { margin: 0 0 14px; font-size: 14.3px; line-height: 18.3px; }
  .founder-quote { font-size: 19px !important; font-weight: 700; margin-top: 4px !important; }

  .mission { position: absolute; left: 31px; top: 560px; width: 888px; height: 103px; border: 4px solid var(--navy); box-sizing: border-box; }
  .mission-title { position: absolute; left: 50%; top: -22px; transform: translateX(-50%); background: var(--white); padding: 0 14px; margin: 0; font-size: 29px; font-weight: 700; white-space: nowrap; }
  .mission p { margin: 14px 24px 0; text-align: center; font-size: 14.3px; line-height: 18.3px; font-weight: 700; }

  .pillar { position: absolute; top: 681px; width: 295px; height: 421px; background: var(--slate); }
  .pillar-one { left: 27px; } .pillar-two { left: 329px; } .pillar-three { left: 630px; }
  .pillar-image { position: absolute; left: 16px; top: 15px; width: 257px; height: 155px; border: 4px solid var(--navy); border-top-width: 3px; border-left-width: 3px; box-shadow: 4px 4px 0 var(--navy); }
  .image-shore { background: linear-gradient(180deg, #e8ecef 0%, #c9c3b6 55%, #d8c6a8 100%); }
  .image-blossom { background: radial-gradient(circle at 45% 50%, #e7a6c6 0%, #c0487a 40%, #3a1f26 100%); }
  .image-summit { background: linear-gradient(180deg, #f2b25a 0%, #f58a2a 55%, #b8471a 100%); }
  .pillar p { position: absolute; left: 26px; top: 200px; width: 234px; margin: 0; font-size: 13.4px; line-height: 16.5px; }

  .footer-rule { position: absolute; left: 0; top: 1121px; width: 950px; height: 5px; background: var(--navy); }
  .footer { position: absolute; left: 0; top: 1132px; width: 950px; height: 68px; background: var(--navy); color: var(--white); text-align: center; font-size: 25px; font-weight: 700; line-height: 64px; white-space: nowrap; }
</style>
</head>
<body>
<main class="flyer">
  <svg class="header-wave" viewBox="0 0 950 250" aria-hidden="true">
    <path d="M0 184 C 160 200, 330 245, 560 236 C 720 230, 850 225, 950 240 L950 250 L0 250 Z" fill="var(--white)"/>
    <path d="M0 176 C 150 205, 320 240, 520 240 C 620 240, 700 232, 780 228 C 580 250, 300 245, 0 200 Z" fill="var(--grey-wave)"/>
    <path d="M0 0 H950 V240 C 870 215, 790 205, 680 210 C 520 220, 420 228, 300 212 C 180 198, 80 180, 0 176 Z" fill="var(--navy)"/>
  </svg>
  <div class="brand-mark" aria-hidden="true"></div>
  <div class="brand-name">Bright Meadow</div>

  <div class="portrait" role="img" aria-label="Portrait photo of the founder in a white knit sweater and dark blazer against a brick wall"></div>
  <section class="founder">
    <h1 class="founder-name">Maria Lindqvist Hale</h1>
    <p>I am a modern mystic and leadership developer who has trained several hundreds of leaders on eg. Harbor Lane, Mossgård Foods, Pinecrest Brewing, Tallow Shoes, Stillwater Cover, Gale Turbines, Linkwave. I have been on my spiritual journey since childhood, meditated since I was 16 and after a decade of extreme skiing and rock climbing I have weighted my adult professional life on the spiritual awakening and to coach people to a more living life.</p>
    <p>With BRIGHT MEADOW I offer opportunities for you as a woman to strengthen contact with your inner being and your own very holy wisdom. To unite the interior with the exterior and deepen your leadership, both as a private person and in your professional role. You are very welcome!</p>
    <p class="founder-quote">"I live as I learn, that's my strength."</p>
  </section>

  <section class="mission">
    <h2 class="mission-title">BRIGHT MEADOW</h2>
    <p>We have become good at performing at the expense of contact with our body and soul, when we really need the opposite. A holistic leadership of people who have good self-knowledge, who grow in the challenges, people who know that vulnerability gives an incomparable strength and does not underestimate their brilliant intellect. The world needs people who live and lead from a whole new place. The show feminine can lead us there.</p>
  </section>

  <article class="pillar pillar-one">
    <div class="pillar-image image-shore" role="img" aria-label="Photo of a thoughtful grey-haired woman standing on a beach"></div>
    <p>As modern women, many of us share a basic pattern of just pushing through and biting, delivering and being good by driving over both body and soul. What if there is another way to get results? A way in which you combine practical skills in leadership such as goals, performance management and coaching with presence in both body, heart and soul. A way that lets soul, heart, achievement and business go hand in hand.</p>
  </article>
  <article class="pillar pillar-two">
    <div class="pillar-image image-blossom" role="img" aria-label="Close-up photo of pink cherry blossoms"></div>
    <p>Before spirituality became its own concept and concept, before the word even emerged or religions and new age seized it, it already existed as a natural part of our lives. We are all valuable just by being, without performing. We are all in contact with something bigger, everything is connected and is part of the same being. Life is sacred. Remembering and living this is spirituality for me.</p>
  </article>
  <article class="pillar pillar-three">
    <div class="pillar-image image-summit" role="img" aria-label="Photo of a caped figure silhouetted on a hilltop at sunset"></div>
    <p>We live in a culture that teaches us to shut down, keep the cover on our dreams and constantly put what is most important to us at the bottom of the list, while we are rushing towards a future that promises us all that we do not take time till now. Bright Meadow is a context that strengthens you, both as being and woman to wake up, grow and succeed with what you want to live before you die. It's empowerment!</p>
  </article>

  <div class="footer-rule"></div>
  <footer class="footer">0700-55 12 34 | WWW.BRIGHTMEADOW.SE | Folj oss pa: Friendline</footer>
</main>
</body>
</html>
```